Business Card and Letterhead Design Project

We need a business card template and letterhead designed for our new business.
Business Card
The information on the business card will be:
Logo
"slogan" - A fresh way to grow savings
Person's Name
Title
Phone Number
Email Address
Website
We strive to make everything SIMPLE so please keep that in mind.
If you want to design something that would go on an odd shaped business card, that is fine, we are up for any ideas.
The Letterhead would have:
logo
business address
phone
fax
website
Here is a link to our logo files: http://qlnk.example/8rTw2Vp
we can provide the winning designer with higher quality files if needbe.

```html
<!DOCTYPE html>
<html lang="en">
<head>
<meta charset="utf-8">
<title>sprouta business card</title>
<link href="https://fonts.googleapis.com/css2?family=Source+Sans+3:wght@400;600;700&display=swap" rel="stylesheet">
<style>
  :root {
    --backdrop: #e8e6e3;
    --card: #ffffff;
    --green: #7cb740;
    --green-faint: #f1f6ec;
    --ink: #474747;
    --ink-soft: #3a3a3a;
    --rule: #c9c9c9;
  }
  * { margin: 0; padding: 0; box-sizing: border-box; }
  html, body {
    width: 1200px; height: 1056px; overflow: hidden;
    background: var(--backdrop);
    font-family: "Source Sans 3", "Helvetica Neue", Arial, sans-serif;
  }
  .canvas { position: relative; width: 1200px; height: 1056px; }
  .card {
    position: absolute; width: 478px; height: 838px;
    background: var(--card); overflow: hidden;
    box-shadow: 0 4px 14px rgba(0,0,0,.18);
  }
  .card-front { left: 105px; top: 102px; }
  .card-back { left: 627px; top: 99px; }

  .front-mark {
    position: absolute; left: 64px; top: 218px;
    width: 350px; height: 408px; border-radius: 50%;
    background: var(--green-faint);
  }
  .front-wordmark {
    position: absolute; left: 0; right: 0; top: 362px;
    text-align: center; font-weight: 700; font-size: 100px;
    letter-spacing: -2px; color: var(--ink); line-height: 1;
  }
  .website {
    position: absolute; left: 0; right: 0; text-align: center;
    font-size: 21px; letter-spacing: 4.5px; color: var(--ink-soft);
  }
  .card-front .website { top: 784px; }

  .person {
    position: absolute; left: 0; right: 0; top: 34px; text-align: center;
    font-size: 20px; color: var(--ink-soft);
  }
  .person-name { font-weight: 700; font-size: 26px; color: var(--green); }

  .brand-lockup {
    position: absolute; left: 40px; top: 310px;
    display: flex; align-items: center; gap: 16px;
  }
  .brand-dot { width: 64px; height: 64px; border-radius: 50%; background: var(--green); }
  .brand-divider { width: 2px; height: 124px; background: var(--rule); }
  .brand-name {
    font-weight: 700; font-size: 80px; letter-spacing: -1px;
    color: var(--ink); line-height: 1;
  }

  .contacts {
    position: absolute; left: 0; right: 0; top: 600px;
    display: flex; justify-content: center; gap: 20px;
    font-size: 20px; color: var(--ink-soft);
  }
  .contact { display: flex; align-items: center; gap: 8px; }
  .contact svg { width: 18px; height: 18px; }
  .card-back .website { top: 648px; }

  .wave { position: absolute; left: 0; top: 0; }
  .slogan {
    position: absolute; left: 0; right: 0; top: 796px; text-align: center;
    font-size: 21px; color: #ffffff;
  }
</style>
</head>
<body>
<div class="canvas">

  <section class="card card-front">
    <div class="front-mark" aria-hidden="true"></div>
    <div class="front-wordmark">sprouta</div>
    <div class="website">www.sprouta.example</div>
  </section>

  <section class="card card-back">
    <p class="person"><span class="person-name">Person's Name,</span> Title</p>

    <div class="brand-lockup">
      <div class="brand-dot" aria-hidden="true"></div>
      <div class="brand-divider" aria-hidden="true"></div>
      <div class="brand-name">sprouta</div>
    </div>

    <div class="contacts">
      <span class="contact">
        <svg viewBox="0 0 20 20" aria-hidden="true">
          <circle cx="10" cy="10" r="9" fill="var(--green)"/>
          <path d="M7 5.5c-1 1-.8 3 1 5.5s4 3.6 5 3l1-1-1.8-1.8-1 .8c-.8-.3-2.2-1.8-2.5-2.6l.8-1L7.8 4.8z" fill="#fff"/>
        </svg>
        123-456-7890
      </span>
      <span class="contact">
        <svg viewBox="0 0 20 20" aria-hidden="true">
          <path d="M2 8l8-5 8 5v9H2z" fill="var(--green)"/>
          <path d="M2 8l8 5 8-5" fill="none" stroke="#fff" stroke-width="1.5"/>
        </svg>
        info@sprouta.example
      </span>
    </div>
    <div class="website">www.sprouta.example</div>

    <svg class="wave" width="478" height="838" viewBox="0 0 478 838" aria-hidden="true">
      <path d="M0 738 C120 790 320 738 478 740 L478 838 L0 838 Z" fill="var(--green)"/>
      <path d="M0 722 C130 784 320 728 478 728" fill="none" stroke="var(--ink)" stroke-width="4"/>
    </svg>
    <p class="slogan">A fresh way to grow savings</p>
  </section>

</div>
</body>
</html>
```